Accounting firm needing business card / letterhead designed
Marcus L. Trenholm, CPA
marcus@veltrowledger.com
www.veltrowledger.com
842 E Alder Ave Maplecrest, IN 43827
419-562-0974

```html
<!DOCTYPE html>
<html lang="en">
<head>
<meta charset="utf-8">
<title>Veltro Ledger – Business Card</title>
<link rel="stylesheet" href="https://fonts.googleapis.com/css2?family=Orbitron:wght@700;900&family=Roboto:wght@400&display=swap">
<style>
  :root {
    --navy: #262262;
    --green: #8dc63f;
    --card-white: #f3f3f3;
    --backdrop: #c9c9c9;
    --white: #ffffff;
  }
  * { margin: 0; padding: 0; box-sizing: border-box; }
  html, body {
    width: 1200px;
    height: 960px;
    overflow: hidden;
    background: var(--backdrop);
  }
  .card {
    position: absolute;
    left: 320px;
    width: 600px;
    height: 342px;
    border-radius: 22px;
    overflow: hidden;
  }
  .card--front {
    top: 108px;
    background: var(--navy);
  }
  .card--back {
    top: 493px;
    background: var(--card-white);
  }
  .brand-name {
    position: absolute;
    left: 0;
    width: 100%;
    text-align: center;
    font-family: "Orbitron", sans-serif;
    font-weight: 700;
    font-size: 36px;
    letter-spacing: 2px;
    line-height: 1;
  }
  .card--front .brand-name { top: 145px; color: var(--white); }
  .card--back .brand-name { top: 124px; color: var(--navy); }
  .front-web {
    position: absolute;
    top: 281px;
    left: 0;
    width: 100%;
    text-align: center;
    font-family: "Roboto", sans-serif;
    font-size: 15px;
    letter-spacing: 6.5px;
    color: var(--white);
  }
  .holder-name {
    position: absolute;
    top: 30px;
    right: 28px;
    font-family: "Orbitron", sans-serif;
    font-weight: 900;
    font-size: 16px;
    letter-spacing: 0.8px;
    color: var(--navy);
  }
  .contact-band {
    position: absolute;
    left: 0;
    top: 243px;
    width: 600px;
    height: 99px;
  }
  .contact-list {
    position: absolute;
    left: 33px;
    top: 262px;
    list-style: none;
    font-family: "Roboto", sans-serif;
    font-size: 15px;
    color: var(--white);
  }
  .contact-list li {
    display: flex;
    align-items: center;
    gap: 8px;
    height: 19.5px;
  }
  .contact-list svg { width: 13px; height: 13px; fill: var(--white); }
  .address {
    position: absolute;
    right: 27px;
    top: 282px;
    text-align: right;
    font-family: "Roboto", sans-serif;
    font-style: normal;
    font-size: 15px;
    line-height: 19.5px;
    color: var(--white);
  }
</style>
</head>
<body>

<section class="card card--front">
  <div class="brand-name">VELTRO LEDGER</div>
  <div class="front-web">www.veltrowledger.com</div>
</section>

<section class="card card--back">
  <div class="holder-name">MARCUS L. TRENHOLM, CPA</div>
  <div class="brand-name">VELTRO LEDGER</div>

  <svg class="contact-band" viewBox="0 0 600 99" aria-hidden="true">
    <rect x="0" y="0" width="600" height="99" fill="var(--navy)"/>
    <polygon points="308,0 600,0 600,99 308,99 270,50" fill="var(--green)"/>
  </svg>

  <ul class="contact-list">
    <li>
      <svg viewBox="0 0 24 24"><path d="M6.6 10.8a15.1 15.1 0 0 0 6.6 6.6l2.2-2.2c.3-.3.7-.4 1-.2 1.1.4 2.3.6 3.6.6.6 0 1 .4 1 1V20c0 .6-.4 1-1 1A17 17 0 0 1 3 4c0-.6.4-1 1-1h3.5c.6 0 1 .4 1 1 0 1.3.2 2.5.6 3.6.1.3 0 .7-.2 1z"/></svg>
      419-562-0974
    </li>
    <li>
      <svg viewBox="0 0 24 24"><path d="M2 5h20v14H2z"/><path d="M2 5l10 8 10-8" fill="none" stroke="var(--navy)" stroke-width="2"/></svg>
      marcus@veltrowledger.com
    </li>
    <li>
      <svg viewBox="0 0 24 24"><circle cx="12" cy="12" r="10"/><path d="M7 8c2 0 3 1 3 3s-2 2-2 4M14 5c0 2 2 2 2 4s2 2 3 2M13 19c0-2 2-3 3-4" fill="none" stroke="var(--navy)" stroke-width="1.8"/></svg>
      www.veltrowledger.com
    </li>
  </ul>

  <address class="address">
    842 E Alder Ave<br>
    Maplecrest, IN 43827
  </address>
</section>

</body>
</html>
```